Australian Trucking Company Requires Professional Looking Stationary

We require a professional looking stationary design that incorporates our newly designed logo.

Our business, called "Brell Haulage Contracting", provides contracting work, transport and logistics to business in Western Australia particularly with links to the mining sector.

We are a small business looking to expand and our new logo and our new stationary will help develop our brand image in our market place.

Target Market(s)

Businesses and Corporation with links to the Mining Sector

Industry/Entity Type

Small Business

Requirements
Must have
• The letterhead must have the following details:
The new logo

Text saying: "Brell Holdings Pty Ltd (ACN 582 316 907) ATF The Brell Discretionary Trust T/AS"
"ABN 71 834 209 553"
Address "P.O Box 817 Wattlegrove WA, 6958"
Phone: 08 9352 7140
Email: brellhaul@mailbox-example.com.au

The text on the letterhead should be editable as the details are likely to change in the near future. Provision should be made for a website address all though one isn't available at the moment.

The styling, layout and font text is entirely up to the designer.

```html
<!DOCTYPE html>
<html lang="en">
<head>
<meta charset="utf-8">
<title>Brell Haulage Contracting – Business Cards</title>
<link rel="stylesheet" href="https://fonts.googleapis.com/css2?family=Source+Sans+3:wght@400;600;700&display=swap">
<style>
  :root {
    --backdrop: #ece8e3;
    --card: #ffffff;
    --brand-red: #c41e2a;
    --ink: #4a4a4a;
    --ink-strong: #3a3a3a;
    --mark-grey: #6d6d6d;
    --rule: #cfcfcf;
  }
  * { box-sizing: border-box; margin: 0; padding: 0; }
  html, body {
    width: 1200px;
    height: 407px;
    overflow: hidden;
    background: var(--backdrop);
    font-family: "Source Sans 3", Arial, sans-serif;
  }
  .stage {
    position: relative;
    width: 1200px;
    height: 407px;
  }
  .card {
    position: absolute;
    top: 60px;
    width: 504px;
    height: 288px;
    background: var(--card);
    box-shadow: 0 2px 6px rgba(0, 0, 0, 0.18);
  }
  .card--front { left: 58px; }
  .card--back  { left: 638px; }

  .brand {
    position: absolute;
    left: 86px;
    display: flex;
    align-items: center;
    gap: 22px;
  }
  .card--front .brand { top: 62px; }
  .card--back .brand  { top: 34px; }

  .brand__dot {
    width: 76px;
    height: 76px;
    border-radius: 50%;
    background: var(--mark-grey);
    flex: none;
  }
  .brand__name {
    color: var(--brand-red);
    font-weight: 700;
    font-size: 25px;
    line-height: 25px;
    text-transform: uppercase;
    letter-spacing: 1px;
  }

  .identity {
    position: absolute;
    right: 252px;
    top: 174px;
    text-align: right;
    color: var(--ink);
    font-size: 13.5px;
    line-height: 24px;
  }
  .identity__name {
    font-size: 17px;
    font-weight: 700;
    color: var(--ink-strong);
  }
  .identity__title {
    font-size: 13.5px;
    font-weight: 400;
  }

  .divider {
    position: absolute;
    left: 259px;
    top: 174px;
    width: 1px;
    height: 72px;
    background: var(--rule);
  }

  .contact {
    position: absolute;
    left: 276px;
    top: 176px;
    list-style: none;
    color: var(--ink);
    font-size: 13.5px;
    line-height: 25px;
  }
  .contact__label {
    color: var(--brand-red);
    font-weight: 700;
    margin-right: 4px;
  }

  .web {
    position: absolute;
    left: 0;
    right: 0;
    top: 258px;
    text-align: center;
    color: var(--ink);
    font-size: 14px;
    font-weight: 700;
    letter-spacing: 3px;
  }
</style>
</head>
<body>
<main class="stage">
  <section class="card card--front" aria-label="Business card front">
    <div class="brand">
      <span class="brand__dot"></span>
      <div class="brand__name">Brell<br>Haulage<br>Contracting</div>
    </div>

    <div class="identity">
      <p><span class="identity__name">Your Name</span> <span class="identity__title">/ Title</span></p>
      <p>P.O Box 817 Wattlegrove WA, 6958</p>
      <p>ABN 71 834 209 553</p>
    </div>

    <div class="divider"></div>

    <ul class="contact">
      <li><span class="contact__label">Phone:</span> 08 9352 7140</li>
      <li><span class="contact__label">Email:</span> brellhaul@mailbox-example.com.au</li>
      <li><span class="contact__label">Web:</span> www.brellhaulage.com.au</li>
    </ul>
  </section>

  <section class="card card--back" aria-label="Business card back">
    <div class="brand">
      <span class="brand__dot"></span>
      <div class="brand__name">Brell<br>Haulage<br>Contracting</div>
    </div>
    <p class="web">www.brellhaulage.com.au</p>
  </section>
</main>
</body>
</html>
```